New Wix logo and website layout

I need a new logo design and a new, modern website layout design. I am a professional therapist providing remedial massage. I am Canadian but live in Australia & would like the logo to have a somewhat 'Canadian feel' to it (something subtle i.e. no flags) I currently have a maple tree leaf as my logo. my current website is tidewaterbodywork.com.au. I need the website to work on mobile phones & traditional web browsers.

Target Market(s)

customers looking for remedial massage and manual lymphatic drainage

Industry/Entity Type

professional massage

Coding

Coded - Design and coding required

Font styles to use
Sans Serif

Colors
EB3D1F
EC4F4E
F09395
F8D3D4
FCEDEE

Requirements
Nice to have
• something subtle that indicates that I am canadian
Should not have
• no flags. nothing too bold

```html
<!DOCTYPE html>
<html lang="en">
<head>
<meta charset="utf-8">
<title>Fees – Tidewater Bodywork</title>
<link href="https://fonts.googleapis.com/css2?family=Libre+Baskerville:ital,wght@0,400;0,700;1,400&family=Poppins:wght@400;500;600&display=swap" rel="stylesheet">
<style>
:root{
  --red:#eb3d1f;
  --coral:#ec4f4e;
  --pink:#f09395;
  --blush:#f8d3d4;
  --cream:#fcedee;
  --ink:#222;
  --white:#fff;
}
*{margin:0;padding:0;box-sizing:border-box}
html,body{width:1200px;height:2470px;overflow:hidden;background:var(--white)}
body{position:relative;font-family:"Poppins",sans-serif;color:var(--ink)}
.serif{font-family:"Libre Baskerville",serif}
.abs{position:absolute}

.topbar{left:0;top:0;width:1200px;height:52px;background:var(--coral);color:var(--white)}
.social{display:flex;gap:22px;align-items:center}
.social span{width:24px;height:24px;border-radius:50%;border:2px solid var(--white)}
.topbar .social{left:76px;top:14px}
.topbar .contact{right:72px;top:13px;display:flex;gap:26px;font-size:20px;align-items:center}
.topbar .contact div{display:flex;gap:10px;align-items:center}

.header{left:0;top:52px;width:1200px;height:105px;background:var(--white)}
.brand{left:75px;top:16px;display:flex;align-items:center;gap:12px}
.brand-mark{width:64px;height:64px;border-radius:50%;border:5px solid var(--red)}
.brand-name{font-family:"Libre Baskerville",serif;font-weight:700;font-size:30px;line-height:35px;color:#333;letter-spacing:.5px}
.nav{right:72px;top:44px;display:flex;gap:38px;font-family:"Libre Baskerville",serif;font-weight:700;font-size:15px;letter-spacing:.5px;color:#222}
.nav .active{color:var(--coral)}

.hero{left:0;top:157px;width:1200px;height:358px;background:linear-gradient(100deg,#d9c2ad 0%,#c8a58c 40%,#b08368 70%,#7e6a5c 100%)}
.hero h1{position:absolute;left:76px;top:140px;font-family:"Libre Baskerville",serif;font-weight:700;font-size:68px;color:var(--white);letter-spacing:2px}

.section-title{left:0;width:1200px;text-align:center;top:582px;font-family:"Libre Baskerville",serif;font-weight:700;font-size:38px;letter-spacing:2px;color:var(--red)}

.card{width:260px;text-align:center}
.card svg{display:block;margin:0 auto}
.card .label{margin-top:40px;font-family:"Libre Baskerville",serif;font-weight:700;font-size:19px;line-height:29px;color:var(--red);letter-spacing:.5px}
.card .price{margin-top:6px;font-family:"Libre Baskerville",serif;font-weight:700;font-size:23px;color:#222}

.note{left:0;width:1200px;top:1575px;text-align:center;font-family:"Libre Baskerville",serif;font-style:italic;font-size:24px;line-height:38px;letter-spacing:.8px;color:#222}

.contact-band{left:0;top:1729px;width:1200px;height:587px;background:linear-gradient(120deg,#c92c18 0%,#d9381f 45%,#c6301a 75%,#b3291a 100%)}
.band-title{font-family:"Libre Baskerville",serif;font-weight:700;font-size:39px;line-height:46px;letter-spacing:2px;color:var(--white)}
.info-row{left:75px;display:flex;align-items:center;gap:20px;color:var(--white);font-size:21px}
.icon-ring{width:54px;height:54px;border-radius:50%;border:2px solid var(--white);display:flex;align-items:center;justify-content:center;flex:none}
.info-name{font-weight:600;font-size:24px;line-height:32px}
.field{background:var(--white);font-size:14px;color:#333;padding:22px 12px 0;height:57px}
.submit{left:616px;top:2173px;width:248px;height:57px;background:var(--pink);color:var(--white);font-family:"Libre Baskerville",serif;font-weight:700;font-size:19px;letter-spacing:1px;display:flex;align-items:center;justify-content:center}

.footer-nav{left:77px;top:2360px;display:flex;gap:38px;font-family:"Libre Baskerville",serif;font-weight:700;font-size:15px;letter-spacing:.5px;color:#222}
.footer-nav .active{color:var(--coral)}
.copyright{left:77px;top:2400px;font-size:13px;color:#333}
.member{left:902px;top:2340px;font-size:17px;color:var(--coral)}
.badge{left:875px;top:2370px;width:250px;height:60px;border-radius:6px;background:#e8efdb}
</style>
</head>
<body>

<div class="abs topbar">
  <div class="abs social"><span></span><span></span><span></span><span></span><span></span></div>
  <div class="abs contact">
    <div>
      <svg width="18" height="18" viewBox="0 0 24 24"><path fill="#fff" d="M6.6 10.8a15 15 0 0 0 6.6 6.6l2.2-2.2a1 1 0 0 1 1-.25 11.4 11.4 0 0 0 3.6.57 1 1 0 0 1 1 1V20a1 1 0 0 1-1 1A17 17 0 0 1 3 4a1 1 0 0 1 1-1h3.5a1 1 0 0 1 1 1c0 1.25.2 2.45.57 3.6a1 1 0 0 1-.25 1z"/></svg>
      0400 555 218
    </div>
    <div>
      <svg width="22" height="16" viewBox="0 0 22 16"><rect width="22" height="16" rx="2" fill="#fff"/><path d="M1 1l10 8 10-8" fill="none" stroke="#ec4f4e" stroke-width="2"/></svg>
      mara@tidewaterbodywork.com.au
    </div>
  </div>
</div>

<div class="abs header">
  <div class="abs brand">
    <div class="brand-mark"></div>
    <div class="brand-name">TIDEWATER<br>BODYWORK</div>
  </div>
  <nav class="abs nav"><span>HOME</span><span>REMEDIAL MASSAGE</span><span>ABOUT ME</span><span class="active">FEES</span><span>CONTACT</span></nav>
</div>

<div class="abs hero" role="img" aria-label="Woman relaxing face down during a hot stone massage">
  <h1>FEES</h1>
</div>

<h2 class="abs section-title">PRICING</h2>

<div class="abs card" style="left:66px;top:665px">
  <svg width="240" height="277" viewBox="0 0 240 277" role="img" aria-label="Therapist stretching a client's arm"><polygon points="120,0 240,69 240,208 120,277 0,208 0,69" fill="var(--red)"/><polygon points="120,13 229,76 229,201 120,264 11,201 11,76" fill="#d8c3b4"/></svg>
  <div class="label">30 MIN<br>REMEDIAL MASSAGE</div><div class="price">$70</div>
</div>
<div class="abs card" style="left:334px;top:665px">
  <svg width="240" height="277" viewBox="0 0 240 277" role="img" aria-label="Hands massaging a client's upper back"><polygon points="120,0 240,69 240,208 120,277 0,208 0,69" fill="var(--red)"/><polygon points="120,13 229,76 229,201 120,264 11,201 11,76" fill="#9a6a52"/></svg>
  <div class="label">40 MIN<br>REMEDIAL MASSAGE</div><div class="price">$90</div>
</div>
<div class="abs card" style="left:607px;top:665px">
  <svg width="240" height="277" viewBox="0 0 240 277" role="img" aria-label="Client relaxing during a shoulder massage"><polygon points="120,0 240,69 240,208 120,277 0,208 0,69" fill="var(--red)"/><polygon points="120,13 229,76 229,201 120,264 11,201 11,76" fill="#e2cbbb"/></svg>
  <div class="label">60 MIN<br>REMEDIAL MASSAGE</div><div class="price">$110</div>
</div>
<div class="abs card" style="left:875px;top:665px">
  <svg width="240" height="277" viewBox="0 0 240 277" role="img" aria-label="Therapist massaging a client's lower back"><polygon points="120,0 240,69 240,208 120,277 0,208 0,69" fill="var(--red)"/><polygon points="120,13 229,76 229,201 120,264 11,201 11,76" fill="#e6d8cf"/></svg>
  <div class="label">90 MIN<br>REMEDIAL MASSAGE</div><div class="price">$160</div>
</div>
<div class="abs card" style="left:460px;top:1120px">
  <svg width="240" height="277" viewBox="0 0 240 277" role="img" aria-label="Therapist performing lymphatic drainage on the abdomen"><polygon points="120,0 240,69 240,208 120,277 0,208 0,69" fill="var(--red)"/><polygon points="120,13 229,76 229,201 120,264 11,201 11,76" fill="#eadbd0"/></svg>
  <div class="label">MANUAL LYMPHATIC<br>DRAINAGE</div><div class="price">$140</div>
</div>

<p class="abs note">I am registered with most health funds. Check your level of cover<br>to see if you are able to claim for remedial massage.</p>

<div class="abs contact-band" role="img" aria-label="Red toned background of a relaxing massage"></div>
<h3 class="abs band-title" style="left:77px;top:1808px">CONTACT<br>INFORMATION</h3>
<h3 class="abs band-title" style="left:614px;top:1808px">QUICK<br>CONTACT FORM</h3>

<div class="abs info-row" style="top:1932px">
  <div class="icon-ring"><svg width="22" height="22" viewBox="0 0 24 24"><path fill="#fff" d="M12 2a7 7 0 0 0-7 7c0 5 7 13 7 13s7-8 7-13a7 7 0 0 0-7-7zm0 9.5A2.5 2.5 0 1 1 12 6.5a2.5 2.5 0 0 1 0 5z"/></svg></div>
  <div><div class="info-name">Mara Ellison</div><div>24 Harbour Lane Seaview VIC 3199</div></div>
</div>
<div class="abs info-row" style="top:2019px">
  <div class="icon-ring"><svg width="20" height="20" viewBox="0 0 24 24"><path fill="#fff" d="M6.6 10.8a15 15 0 0 0 6.6 6.6l2.2-2.2a1 1 0 0 1 1-.25 11.4 11.4 0 0 0 3.6.57 1 1 0 0 1 1 1V20a1 1 0 0 1-1 1A17 17 0 0 1 3 4a1 1 0 0 1 1-1h3.5a1 1 0 0 1 1 1c0 1.25.2 2.45.57 3.6a1 1 0 0 1-.25 1z"/></svg></div>
  <div>0400 555 218</div>
</div>
<div class="abs info-row" style="top:2106px">
  <div class="icon-ring"><svg width="20" height="15" viewBox="0 0 22 16"><rect width="22" height="16" rx="2" fill="#fff"/><path d="M1 1l10 8 10-8" fill="none" stroke="#d9381f" stroke-width="2"/></svg></div>
  <div>mara@tidewaterbodywork.com.au</div>
</div>
<div class="abs social" style="left:77px;top:2203px"><span></span><span></span><span></span><span></span><span></span></div>

<div class="abs field" style="left:616px;top:1919px;width:248px">Name</div>
<div class="abs field" style="left:879px;top:1919px;width:248px">Email Address</div>
<div class="abs field" style="left:616px;top:1990px;width:248px">Phone No</div>
<div class="abs field" style="left:879px;top:1990px;width:248px;display:flex;justify-content:space-between">Select Date
  <svg width="14" height="14" viewBox="0 0 14 14"><rect x="1" y="2" width="12" height="11" fill="none" stroke="#333" stroke-width="1.5"/><rect x="1" y="2" width="12" height="3" fill="#333"/></svg>
</div>
<div class="abs field" style="left:616px;top:2061px;width:511px;height:98px">Message</div>
<div class="abs submit">SUBMIT</div>

<nav class="abs footer-nav"><span class="active">HOME</span><span>REMEDIAL MASSAGE</span><span>ABOUT ME</span><span>FEES</span><span>CONTACT</span></nav>
<div class="abs copyright">Copyright© 2022 Company Name&nbsp; All Right Reserved</div>
<div class="abs member">Member</div>
<div class="abs badge"></div>

</body>
</html>
```